Business card for medical clinic

I need an upmarket, modern medical/health business card for my clinic

Contact Information for Business Card

name, address, email, qr code

```html
<!DOCTYPE html>
<html lang="en">
<head>
<meta charset="utf-8">
<title>Meridale Health Partners – Business Card</title>
<link href="https://fonts.googleapis.com/css2?family=Tinos:wght@400;700&display=swap" rel="stylesheet">
<style>
  :root {
    --page-bg: #e6e7ea;
    --card-white: #ffffff;
    --card-white-shade: #eeeeef;
    --navy: #1a2540;
    --brand-blue: #2a9fd6;
    --ink-navy: #1c2a4a;
    --text-light: #f2f4f8;
  }
  * { box-sizing: border-box; margin: 0; padding: 0; }
  html, body {
    width: 1200px; height: 900px; overflow: hidden;
    background: var(--page-bg);
    font-family: "Tinos", "Times New Roman", serif;
  }
  .canvas {
    position: relative; width: 1200px; height: 900px;
    display: flex; flex-direction: column; align-items: center; justify-content: center; gap: 50px;
  }
  .card {
    position: relative; width: 580px; height: 340px;
    box-shadow: 0 10px 28px rgba(20, 30, 50, 0.18);
    overflow: hidden;
  }
  .card--front {
    background: linear-gradient(120deg, var(--card-white-shade) 0%, var(--card-white) 70%);
    border-radius: 34px 0 34px 0;
  }
  .card--back {
    background: var(--navy);
    border-radius: 0 34px 0 34px;
  }
  .front-url {
    position: absolute; top: 34px; left: 0; right: 0;
    text-align: center; font-size: 17px; font-weight: 700;
    letter-spacing: 0.42em; color: var(--ink-navy);
  }
  .front-url .domain { color: var(--brand-blue); }
  .brand {
    position: absolute; display: flex; align-items: center; gap: 14px;
  }
  .brand__dot {
    width: 46px; height: 46px; border-radius: 50%; flex: none;
  }
  .brand__name {
    font-size: 28px; font-weight: 400; letter-spacing: 0.06em;
    line-height: 1.05; text-transform: uppercase; white-space: nowrap;
  }
  .card--front .brand { left: 60px; bottom: 70px; }
  .card--front .brand__dot { background: var(--brand-blue); }
  .card--front .brand__name { color: var(--ink-navy); }
  .card--back .brand { right: 34px; bottom: 96px; gap: 12px; }
  .card--back .brand__dot { background: var(--text-light); width: 36px; height: 36px; }
  .card--back .brand__name { color: var(--text-light); font-size: 20px; letter-spacing: 0.05em; }
  .contact {
    position: absolute; left: 40px; top: 50px; color: var(--text-light);
  }
  .contact__name {
    font-size: 21px; font-weight: 700; color: var(--brand-blue); text-transform: uppercase; letter-spacing: 0.01em;
  }
  .contact__role { font-size: 17px; margin-top: 2px; }
  .contact__address { font-size: 15px; line-height: 1.25; margin-top: 22px; }
  .contact__list { list-style: none; margin-top: 22px; }
  .contact__item { display: flex; align-items: center; gap: 10px; font-size: 15px; line-height: 1.6; white-space: nowrap; }
  .contact__icon { width: 15px; height: 15px; flex: none; }
</style>
</head>
<body>
<main class="canvas">
  <section class="card card--front" aria-label="Card front">
    <p class="front-url">www.<span class="domain">meridalehealth</span>.com</p>
    <div class="brand">
      <span class="brand__dot"></span>
      <span class="brand__name">Meridale Health<br>Partners</span>
    </div>
  </section>

  <section class="card card--back" aria-label="Card back">
    <div class="contact">
      <p class="contact__name">Daniel Reyes</p>
      <p class="contact__role">Director</p>
      <p class="contact__address">12 Harbor Lane<br>Westbrook 4020</p>
      <ul class="contact__list">
        <li class="contact__item">
          <svg class="contact__icon" viewBox="0 0 16 16" aria-hidden="true"><path d="M3.2 1.5l2.4 2.6-1.2 1.8c.9 2 2.4 3.6 4.5 4.6l1.8-1.2 2.6 2.4-1.4 2.2C6.8 13.5 2.3 9 1.1 2.9z" fill="#2a9fd6"/></svg>
          555-018-2040
        </li>
        <li class="contact__item">
          <svg class="contact__icon" viewBox="0 0 16 16" aria-hidden="true"><rect x="1" y="3" width="14" height="10" fill="none" stroke="#2a9fd6" stroke-width="1.5"/><path d="M1 3l7 6 7-6" fill="none" stroke="#2a9fd6" stroke-width="1.5"/></svg>
          hello@meridalehealth.com
        </li>
        <li class="contact__item">
          <svg class="contact__icon" viewBox="0 0 16 16" aria-hidden="true"><g fill="none" stroke="#2a9fd6" stroke-width="1.2"><circle cx="8" cy="8" r="6.5"/><ellipse cx="8" cy="8" rx="3" ry="6.5"/><path d="M1.5 8h13M2.5 4.7h11M2.5 11.3h11"/></g></svg>
          www.meridalehealth.com
        </li>
      </ul>
    </div>
    <div class="brand">
      <span class="brand__dot"></span>
      <span class="brand__name">Meridale Health<br>Partners</span>
    </div>
  </section>
</main>
</body>
</html>
```